Snoutsaver.net Dog Coupon Site Website Design

TailThrift - Dog Coupon Site Design Brief

Project Overview
**Site Name:** SnoutSaver.net
**Purpose:** A modern coupon aggregation platform specifically for dog and pet-related products and services
**Target Audience:** Dog owners, pet enthusiasts, budget-conscious pet parents

Brand Identity & Visual Direction

Typography
- **Headers:** Modern sans-serif (Inter or similar) - Clean and friendly
- **Body:** Readable sans-serif with good mobile legibility
- **Accent:** Playful but professional font for coupon codes

Design Principles
- **Flat Design:** Clean, minimal with subtle shadows
- **Friendly & Approachable:** Rounded corners, soft edges
- **Trust-Building:** Clear pricing, transparent savings
- **Scannable:** Easy-to-read coupon codes and offers

## User Experience & Functionality

### Homepage Features
1. **Hero Section**
- Clear value proposition
- Search functionality
- Featured savings highlight

2. **Coupon Cards**
- One-click copy functionality
- Clear discount display
- Store/brand logos
- Expiration dates
- "Get Deal" call-to-action

3. **Navigation**
- Categories (Food, Toys, Health, Services, etc.)
- Popular stores
- Latest deals

### Interactive Elements
- **Copy Button:** Instant feedback when coupon copied
- **Deal Pages:** Detailed offer information, terms, store details
- **Search & Filter:** By category, store, discount amount
- **Mobile Menu:** Hamburger navigation for mobile

## Technical Requirements

### Responsive Design
- **Mobile-First:** Optimized for touch interactions
- **Tablet:** Adapted layout for medium screens
- **Desktop:** Full-width utilization with sidebar potential

### Performance
- **Fast Loading:** Optimized images, minimal JavaScript
- **Accessibility:** WCAG compliant, screen reader friendly
- **SEO Optimized:** Structured data for deals and offers

## Content Strategy

### Deal Categories
- Dog Food & Treats
- Toys & Accessories
- Health & Grooming
- Training & Services
- Outdoor & Travel

### Key Messaging
- "Save on everything your dog loves"
- "Verified deals updated daily"
- "Your pup deserves the best for less"

## Conversion Optimization

### Trust Elements
- Deal verification badges
- User reviews/ratings
- Clear savings calculations
- Expiration date transparency

### Call-to-Actions
- "Copy Code" (primary action)
- "Get Deal" (secondary action)
- "View All [Store] Deals"

## Success Metrics
- Coupon copy rate
- Click-through to retailer
- User return visits
- Mobile vs desktop usage
- Category performance

This design brief ensures a user-friendly, trustworthy platform that makes finding and using pet deals effortless while maintaining a warm, dog-loving community feel.

1. Design Objective
Create a warm, energetic space where dog lovers instantly feel welcomed and confident they’re finding genuine savings for their furry friends. Everything from the layout to the smallest icon should reinforce trust, delight, and simplicity.
2. Visual Personality
Color Palette: Soft, cheerful hues—think warm yellows and gentle blues—that evoke sunshine and playfulness without overwhelming.
Typography:
Headings: A modern, friendly sans‑serif (like Inter) with open letterforms to feel approachable.
Body Copy: Highly legible sans‑serif with generous line spacing for comfort on small screens.
Accent Font: A slightly quirky, hand‑drawn style used sparingly for coupon codes and special call‑outs, giving a personal, “paw‑picked” touch.
Imagery & Icons: Real‑life photographs of happy dogs interspersed with clean line‑icons of bones, paw prints, and hearts. Rounded shapes and subtle shadows keep the look soft and contemporary.
3. Layout & Hierarchy
Hero Area:
Full‑bleed image of a joyful dog, overlaid with a single, punchy tagline (“Save on everything your dog loves”).
Prominent search bar centered to invite exploration.
Offer Grid:
Generous white space around each coupon card so the eye can rest and scan easily.
Coupon cards feature a bold discount label, brand logo, and a friendly “Get Deal” button.
A playful “Copied!” animation briefly replaces the button once the code is grabbed.
Navigation:
A fixed header with clear category labels (Food, Toys, Health, Services).
A secondary “Popular Stores” carousel below to spotlight key partners.
4. Interaction & Motion
Micro‑interactions:
Hover state for cards subtly lifts the card and deepens its shadow, inviting a click.
Copy‑code button pulses once on hover, hinting at its one‑click magic.
Transitions:
Smooth fades between deal filters and search results to reassure users that the site is responding.
Loading indicators shaped like spinning collars or wagging tails to keep the theme consistent.
5. Accessibility & Inclusivity
Ensure all text meets contrast standards so every pet parent—regardless of vision—can read offers with ease.
Interactive elements sized for easy tapping on touchscreens.
Alt‑text for all imagery describing dogs, products, and actions for screen‑reader users.
6. Emotional Tone
From the moment someone lands on SnoutSaver.net, they should feel the joy of treating their dog without guilt. Friendly copy (“Your pup deserves the best for less”) paired with bright visuals will create a sense of community and shared passion.
7. Success by Design
Scan‑ability: Users should spot great deals in under two seconds.
Trust Signals: Badges (“Verified Savings”), clear expiration dates, and reviewer star icons should feel earned and prominent.
Return Visits: A “My Favorite Deals” heart icon encourages saving and returning, reinforced by subtle reminders in the UI.
This design approach keeps dog lovers front and center—making sure every graphic, font choice, and interaction feels like it was lovingly tailored for them.

Target Market(s)

Dog Lovers looking for good deals

Industry/Entity Type

Coupon Code

Number of Pages Required

4 page

Font styles to use
Sans Serif

Requirements
Must have
• Modern look, coupon copy cards it's a deal site and I want the coupon code and copy in the coupon card, blog section, review section, modern footer/header
Nice to have
• Modern coupon code website, easy to use

```html
<!DOCTYPE html>
<html lang="en">
<head>
<meta charset="utf-8">
<title>SnoutSaver.net – Save on everything your dog loves</title>
<link rel="stylesheet" href="https://fonts.googleapis.com/css2?family=Poppins:ital,wght@0,400;0,500;0,600;0,700;1,400&display=swap">
<style>
:root{
  --navy:#2d3a6e;
  --navy-deep:#2b3769;
  --yellow:#fcc10f;
  --orange:#f5895f;
  --blue:#1a6fcc;
  --card-blue:#c7dbf7;
  --band-grey:#f2f2f2;
  --review-blue:#cfe0f7;
  --ink:#222;
  --text:#3a3a3a;
  --white:#fff;
}
*{box-sizing:border-box;margin:0;padding:0}
html,body{width:1200px;height:2942px;overflow:hidden}
body{font-family:"Poppins",sans-serif;color:var(--ink);background:var(--white)}
section,header,footer{position:relative;width:1200px}

/* header */
.site-header{height:82px;background:var(--white);border-bottom:1px solid #e6e6e6}
.brand{position:absolute;left:75px;top:20px;font-size:31px;font-weight:700;color:var(--navy);letter-spacing:-.3px}
.brand span{color:var(--yellow);font-size:22px;font-weight:500}
.main-nav{position:absolute;right:73px;top:32px;display:flex;gap:38px;font-size:15px}
.main-nav a{color:var(--ink);text-decoration:none}
.main-nav a.active{color:var(--yellow);text-decoration:underline;text-underline-offset:4px}

/* hero */
.hero{height:570px;overflow:hidden}
.hero-photo{position:absolute;inset:0;background:radial-gradient(ellipse at 55% 45%,#8a6a3e 0%,#4a4a26 30%,#1f3015 60%,#14200f 100%)}
.hero-title{position:absolute;top:205px;width:100%;text-align:center;color:var(--white);font-size:43px;font-weight:700;text-shadow:0 2px 8px rgba(0,0,0,.35)}
.search-bar{position:absolute;left:164px;top:286px;width:873px;height:69px;background:var(--white);border-radius:35px;display:flex;overflow:hidden;font-size:13px}
.search-field{display:flex;align-items:center;justify-content:space-between;padding:0 16px 0 14px;border-right:1px solid #ddd;color:#222}
.search-field:first-child{padding-left:20px}
.search-field svg{width:8px;height:12px}
.search-btn{flex:1;background:var(--yellow);color:var(--white);font-size:21px;font-weight:600;display:flex;align-items:center;justify-content:center;gap:10px}

/* promo */
.promo{height:91px;background:var(--band-grey)}
.promo-lead{position:absolute;left:260px;top:28px;font-size:27px;font-weight:600;color:#2a2a2a}
.promo-save{position:absolute;left:586px;top:17px;font-size:14px;font-weight:600;color:var(--orange)}
.promo-value{position:absolute;left:585px;top:28px;font-size:39px;font-weight:700;color:var(--blue)}
.btn-yellow{background:var(--yellow);color:var(--white);font-weight:700;display:flex;align-items:center;justify-content:center;text-decoration:none}
.promo .btn-yellow{position:absolute;left:773px;top:18px;width:165px;height:53px;font-size:24px}

/* section headings */
.section-title{position:absolute;left:75px;font-size:34px;font-weight:600;color:#333}
.section-title.center{left:0;width:100%;text-align:center}
.arrow{position:absolute;width:43px;height:43px;border-radius:50%;display:flex;align-items:center;justify-content:center}
.arrow.grey{background:#e7e7e7}
.arrow.yellow{background:var(--yellow)}
.arrow svg{width:12px;height:14px}

/* coupons */
.coupons{height:462px;overflow:hidden}
.coupons .section-title{top:49px}
.coupon-card{position:absolute;top:129px;width:425px;height:249px;background:var(--card-blue);border-radius:16px;overflow:hidden}
.coupon-card.lifted{box-shadow:3px 5px 0 #8fb1de}
.coupon-photo{position:absolute;left:12px;top:8px;width:225px;height:162px;border-radius:10px;background:linear-gradient(135deg,#e9d7c0,#c79a6c 55%,#b6cbe9)}
.save-tag{position:absolute;left:241px;top:18px;width:163px;height:55px;background:var(--orange);color:var(--white);padding:0 12px;line-height:1}
.save-tag small{display:block;font-size:16px;font-weight:600;padding-top:4px}
.save-tag strong{display:block;font-size:33px;font-weight:700;margin-top:1px}
.coupon-desc{position:absolute;left:241px;top:76px;width:180px;font-size:16px;font-weight:500;line-height:23px;color:#333}
.coupon-brand{position:absolute;left:241px;top:120px;font-size:38px;font-weight:700;color:var(--navy)}
.coupon-card .btn-deal{position:absolute;left:241px;top:185px;width:163px;height:51px;background:var(--orange);color:var(--white);font-size:25px;font-weight:700;display:flex;align-items:center;justify-content:center}
.expire{position:absolute;left:20px;top:196px;font-size:12px;font-weight:500;color:#333;line-height:1.3}
.expire b{display:block;font-size:16px;font-weight:500;letter-spacing:.5px}
.code-label{position:absolute;left:147px;top:166px;font-size:14px;font-weight:600;line-height:17px;color:#222}
.code-box{position:absolute;left:147px;top:204px;width:85px;height:32px;border:2px solid var(--navy);font-size:14px;font-weight:600;color:var(--navy);display:flex;align-items:center;justify-content:center}
.code-box.copied{background:#a9a9a9;border-color:#a9a9a9;color:var(--white);font-weight:500}

/* categories */
.categories{height:462px;background:var(--band-grey)}
.categories .section-title{top:62px}
.cat-item{position:absolute;top:133px;width:262px;text-align:center}
.cat-photo{width:192px;height:192px;border-radius:50%;margin:0 auto}
.cat-photo.selected{border:3px solid var(--navy)}
.cat-item p{margin-top:12px;font-size:18px;font-weight:600;color:#333}
.categories .btn-yellow,.stores .btn-yellow{position:absolute;left:522px;width:186px;height:56px;font-size:22px;z-index:2}
.categories .btn-yellow{top:435px}

/* stores */
.stores{height:456px}
.stores .section-title{top:98px}
.store-box{position:absolute;top:163px;width:241px;height:100px;border:1px solid #e3e3e3;display:flex;align-items:center;justify-content:center;font-size:28px;font-weight:700;color:var(--navy)}
.store-box.selected{border:3px solid var(--navy)}
.stores .btn-yellow{top:323px}

/* reviews */
.reviews{height:459px;background:var(--review-blue)}
.reviews .section-title{top:55px}
.review-card{position:absolute;top:162px;width:328px;height:233px;background:var(--white);text-align:center}
.review-card.selected{border:2px solid var(--navy)}
.quote-mark{position:absolute;left:50%;top:-33px;margin-left:-31px;width:62px;height:62px;border-radius:50%;background:var(--orange);display:flex;align-items:center;justify-content:center;color:var(--white);font-size:40px;font-weight:700;line-height:1;padding-top:16px}
.stars{position:absolute;top:48px;width:100%;display:flex;justify-content:center;gap:7px}
.stars svg{width:19px;height:19px}
.review-text{position:absolute;top:78px;left:18px;right:18px;font-size:17.5px;font-style:italic;line-height:27px;color:#333}
.review-name{position:absolute;top:196px;width:100%;font-size:16px;font-weight:600;color:var(--navy)}

/* footer */
.site-footer{height:360px;background:var(--navy-deep);color:var(--white)}
.foot-col{position:absolute;top:58px}
.foot-col h3{font-size:24px;font-weight:600;margin-bottom:12px}
.foot-col p,.foot-col li{font-size:15px;line-height:23px;list-style:none}
.foot-col li{line-height:32px}
.foot-col a.more{display:inline-block;margin-top:12px;color:var(--yellow);font-size:13px;font-weight:600;text-decoration:underline}
.news-field{width:241px;height:46px;border:2px solid var(--white);display:flex;align-items:center;justify-content:space-between;padding:0 12px;font-size:13px}
.badges{display:flex;gap:16px;margin-top:30px}
.badge{width:78px;height:78px;border-radius:50%}
.badge.verified{background:#3eaa4c}
.badge.best{background:var(--yellow)}
.foot-rule{position:absolute;left:0;right:0;top:300px;border-top:1px solid #4b568a}
.copyright{position:absolute;left:75px;top:320px;font-size:12px}
.social{position:absolute;right:72px;top:318px;display:flex;gap:14px;font-size:12px;font-weight:500}
</style>
</head>
<body>

<header class="site-header">
  <div class="brand">SnoutSaver<span>.net</span></div>
  <nav class="main-nav">
    <a href="#" class="active">Home</a>
    <a href="#">Categories</a>
    <a href="#">Popular Stores</a>
    <a href="#">Latest Deals</a>
  </nav>
</header>

<section class="hero">
  <div class="hero-photo" role="img" aria-label="Golden retriever leaping on a lawn toward a tennis ball"></div>
  <h1 class="hero-title">Save on everything your dog loves</h1>
  <form class="search-bar">
    <div class="search-field" style="width:231px">Search keyword</div>
    <div class="search-field" style="width:160px">By Category <svg viewBox="0 0 8 12"><path d="M4 0 8 5H0zM4 12 0 7h8z" fill="#222"/></svg></div>
    <div class="search-field" style="width:116px">Store <svg viewBox="0 0 8 12"><path d="M4 0 8 5H0zM4 12 0 7h8z" fill="#222"/></svg></div>
    <div class="search-field" style="width:215px">Discount Amount <svg viewBox="0 0 8 12"><path d="M4 0 8 5H0zM4 12 0 7h8z" fill="#222"/></svg></div>
    <div class="search-btn"><svg width="22" height="22" viewBox="0 0 22 22"><circle cx="9" cy="9" r="7" fill="none" stroke="#fff" stroke-width="3"/><path d="M14 14l6 6" stroke="#fff" stroke-width="3" stroke-linecap="round"/></svg>Search</div>
  </form>
</section>

<section class="promo">
  <div class="promo-lead">Buy Min 5 Coupons &amp;</div>
  <div class="promo-save">Save</div>
  <div class="promo-value">10% OFF</div>
  <a href="#" class="btn-yellow">Get Deal</a>
</section>

<section class="coupons">
  <h2 class="section-title">Coupon Cards</h2>
  <span class="arrow grey" style="left:1034px;top:55px"><svg viewBox="0 0 12 14"><path d="M8 2 3 7l5 5" fill="none" stroke="#333" stroke-width="1.8"/></svg></span>
  <span class="arrow yellow" style="left:1083px;top:55px"><svg viewBox="0 0 12 14"><path d="M4 2l5 5-5 5" fill="none" stroke="#fff" stroke-width="1.8"/></svg></span>

  <article class="coupon-card lifted" style="left:75px">
    <div class="coupon-photo" role="img" aria-label="Curly-haired dog beside a bag of dog food"></div>
    <div class="save-tag"><small>SAVE:</small><strong>30% OFF</strong></div>
    <p class="coupon-desc">On all premium dog food &amp; treats</p>
    <div class="coupon-brand">Zestly</div>
    <a class="btn-deal">Get Deal</a>
    <div class="expire">Expire On<b>05/06/2025</b></div>
    <div class="code-label">Coupon<br>Code</div>
    <div class="code-box">BARK 30</div>
  </article>

  <article class="coupon-card" style="left:525px">
    <div class="coupon-photo" role="img" aria-label="Small chihuahua lying with a pink chew toy"></div>
    <div class="save-tag"><small>SAVE:</small><strong>30% OFF</strong></div>
    <p class="coupon-desc">On all premium dog food &amp; treats</p>
    <div class="coupon-brand">Zestly</div>
    <a class="btn-deal">Get Deal</a>
    <div class="expire">Expire On<b>05/06/2025</b></div>
    <div class="code-label">Coupon<br>Code</div>
    <div class="code-box copied">COPIED</div>
  </article>

  <article class="coupon-card" style="left:975px">
    <div class="coupon-photo" role="img" aria-label="Fluffy dog beside grooming bottles and brushes"></div>
    <div class="expire">Expire On<b>05/06/2025</b></div>
    <div class="code-label">Coupon<br>Code</div>
    <div class="code-box">BARK 30</div>
  </article>
</section>

<section class="categories">
  <h2 class="section-title center">Deal Categories</h2>
  <span class="arrow yellow" style="left:32px;top:225px"><svg viewBox="0 0 12 14"><path d="M8 2 3 7l5 5" fill="none" stroke="#fff" stroke-width="1.8"/></svg></span>
  <span class="arrow yellow" style="left:1125px;top:225px"><svg viewBox="0 0 12 14"><path d="M4 2l5 5-5 5" fill="none" stroke="#fff" stroke-width="1.8"/></svg></span>

  <div class="cat-item" style="left:75px"><div class="cat-photo" role="img" aria-label="Dog eating kibble from a green bowl" style="background:linear-gradient(140deg,#d8d8d8,#b08450 55%,#8fae3a)"></div><p>Dog Food &amp; Treats</p></div>
  <div class="cat-item" style="left:337px"><div class="cat-photo selected" role="img" aria-label="Border collie with a rope toy" style="background:linear-gradient(140deg,#e6e1d8,#3a3a3a 50%,#d98a3a)"></div><p>Toys &amp; Accessories</p></div>
  <div class="cat-item" style="left:601px"><div class="cat-photo" role="img" aria-label="Long-haired small dog being combed" style="background:linear-gradient(140deg,#cfcfcf,#f0ede8 55%,#8a8a8a)"></div><p>Health &amp; Grooming</p></div>
  <div class="cat-item" style="left:864px"><div class="cat-photo" role="img" aria-label="Dog giving a paw to a hand on grass" style="background:linear-gradient(140deg,#6c9a3c,#e9e2d8 50%,#b4662c)"></div><p>Training &amp; Services</p></div>

  <a href="#" class="btn-yellow">View All</a>
</section>

<section class="stores">
  <h2 class="section-title">Popular Stores</h2>
  <span class="arrow grey" style="left:1034px;top:103px"><svg viewBox="0 0 12 14"><path d="M8 2 3 7l5 5" fill="none" stroke="#333" stroke-width="1.8"/></svg></span>
  <span class="arrow grey" style="left:1083px;top:103px"><svg viewBox="0 0 12 14"><path d="M4 2l5 5-5 5" fill="none" stroke="#333" stroke-width="1.8"/></svg></span>

  <div class="store-box" style="left:75px">Harbor &amp; Gale</div>
  <div class="store-box selected" style="left:343px">ShopWell</div>
  <div class="store-box" style="left:617px">Fernway</div>
  <div class="store-box" style="left:885px">VigorBite</div>

  <a href="#" class="btn-yellow">View All</a>
</section>

<section class="reviews">
  <h2 class="section-title center">Customer Reviews</h2>
  <span class="arrow yellow" style="left:45px;top:257px"><svg viewBox="0 0 12 14"><path d="M8 2 3 7l5 5" fill="none" stroke="#fff" stroke-width="1.8"/></svg></span>
  <span class="arrow yellow" style="left:1108px;top:257px"><svg viewBox="0 0 12 14"><path d="M4 2l5 5-5 5" fill="none" stroke="#fff" stroke-width="1.8"/></svg></span>

  <article class="review-card" style="left:75px">
    <div class="quote-mark">“</div>
    <div class="stars"><svg viewBox="0 0 20 20"><path d="M10 1l2.6 6 6.4.5-4.9 4.2 1.5 6.3L10 14.6 4.4 18l1.5-6.3L1 7.5 7.4 7z" fill="#f7a41b"/></svg><svg viewBox="0 0 20 20"><path d="M10 1l2.6 6 6.4.5-4.9 4.2 1.5 6.3L10 14.6 4.4 18l1.5-6.3L1 7.5 7.4 7z" fill="#f7a41b"/></svg><svg viewBox="0 0 20 20"><path d="M10 1l2.6 6 6.4.5-4.9 4.2 1.5 6.3L10 14.6 4.4 18l1.5-6.3L1 7.5 7.4 7z" fill="#f7a41b"/></svg><svg viewBox="0 0 20 20"><path d="M10 1l2.6 6 6.4.5-4.9 4.2 1.5 6.3L10 14.6 4.4 18l1.5-6.3L1 7.5 7.4 7z" fill="#f7a41b"/></svg><svg viewBox="0 0 20 20"><path d="M10 1l2.6 6 6.4.5-4.9 4.2 1.5 6.3L10 14.6 4.4 18l1.5-6.3L1 7.5 7.4 7z" fill="#f7a41b"/></svg></div>
    <p class="review-text">“ Excepteur sint occaecat cupidatat non proident, sunt in culpa qui officia deserunt mollit anim id est laborum.”</p>
    <div class="review-name">Name Heading</div>
  </article>

  <article class="review-card selected" style="left:437px">
    <div class="quote-mark">“</div>
    <div class="stars"><svg viewBox="0 0 20 20"><path d="M10 1l2.6 6 6.4.5-4.9 4.2 1.5 6.3L10 14.6 4.4 18l1.5-6.3L1 7.5 7.4 7z" fill="#f7a41b"/></svg><svg viewBox="0 0 20 20"><path d="M10 1l2.6 6 6.4.5-4.9 4.2 1.5 6.3L10 14.6 4.4 18l1.5-6.3L1 7.5 7.4 7z" fill="#f7a41b"/></svg><svg viewBox="0 0 20 20"><path d="M10 1l2.6 6 6.4.5-4.9 4.2 1.5 6.3L10 14.6 4.4 18l1.5-6.3L1 7.5 7.4 7z" fill="#f7a41b"/></svg><svg viewBox="0 0 20 20"><path d="M10 1l2.6 6 6.4.5-4.9 4.2 1.5 6.3L10 14.6 4.4 18l1.5-6.3L1 7.5 7.4 7z" fill="#f7a41b"/></svg><svg viewBox="0 0 20 20"><path d="M10 1l2.6 6 6.4.5-4.9 4.2 1.5 6.3L10 14.6 4.4 18l1.5-6.3L1 7.5 7.4 7z" fill="#f7a41b"/></svg></div>
    <p class="review-text">“ Excepteur sint occaecat cupidatat non proident, sunt in culpa qui officia deserunt mollit anim id est laborum.”</p>
    <div class="review-name">Name Heading</div>
  </article>

  <article class="review-card" style="left:796px">
    <div class="quote-mark">“</div>
    <div class="stars"><svg viewBox="0 0 20 20"><path d="M10 1l2.6 6 6.4.5-4.9 4.2 1.5 6.3L10 14.6 4.4 18l1.5-6.3L1 7.5 7.4 7z" fill="#f7a41b"/></svg><svg viewBox="0 0 20 20"><path d="M10 1l2.6 6 6.4.5-4.9 4.2 1.5 6.3L10 14.6 4.4 18l1.5-6.3L1 7.5 7.4 7z" fill="#f7a41b"/></svg><svg viewBox="0 0 20 20"><path d="M10 1l2.6 6 6.4.5-4.9 4.2 1.5 6.3L10 14.6 4.4 18l1.5-6.3L1 7.5 7.4 7z" fill="#f7a41b"/></svg><svg viewBox="0 0 20 20"><path d="M10 1l2.6 6 6.4.5-4.9 4.2 1.5 6.3L10 14.6 4.4 18l1.5-6.3L1 7.5 7.4 7z" fill="#f7a41b"/></svg><svg viewBox="0 0 20 20"><path d="M10 1l2.6 6 6.4.5-4.9 4.2 1.5 6.3L10 14.6 4.4 18l1.5-6.3L1 7.5 7.4 7z" fill="#f7a41b"/></svg></div>
    <p class="review-text">“ Excepteur sint occaecat cupidatat non proident, sunt in culpa qui officia deserunt mollit anim id est laborum.”</p>
    <div class="review-name">Name Heading</div>
  </article>
</section>

<footer class="site-footer">
  <div class="foot-col" style="left:75px;width:250px">
    <h3>SnoutSaver.net</h3>
    <p>Excepteur sint occaecat cupidatat non proident, sunt in culpa qui officia deserunt mollit anim id est laborum.</p>
    <a href="#" class="more">Read More</a>
  </div>
  <div class="foot-col" style="left:363px">
    <h3>Quick Links</h3>
    <ul><li>Categories</li><li>Popular stores</li><li>Latest deals</li></ul>
  </div>
  <div class="foot-col" style="left:601px">
    <h3>Deal Categories</h3>
    <ul><li>Dog Food &amp; Treats</li><li>Toys &amp; Accessories</li><li>Health &amp; Grooming</li><li>Training &amp; Services</li><li>Outdoor &amp; Travel</li></ul>
  </div>
  <div class="foot-col" style="left:885px">
    <h3>Newsletter Sign Up</h3>
    <div class="news-field">Email Address <svg width="18" height="18" viewBox="0 0 18 18"><path d="M1 8 17 1 12 17 9 10z" fill="var(--yellow)"/></svg></div>
    <div class="badges"><span class="badge verified" role="img" aria-label="Verified deal badge"></span><span class="badge best" role="img" aria-label="Best choice badge"></span></div>
  </div>
  <div class="foot-rule"></div>
  <div class="copyright">Copyright © 2025 Company Name All Right Reserved</div>
  <nav class="social"><span>Facepage</span><span>Chirp</span><span>Snaps</span><span>Linkup</span><span>Tubely</span></nav>
</footer>

</body>
</html>
```